I need a business card design for a new dance business. I offer classical Indian dance tuition and also professional performances. I want to offer the community a variety of Indian dance experiences which include: group class and private tuition, school and preschool educational courses and workshops. dance theatre performances, community function workshops and performances, Kids Bollywood parties, wedding & conference performances, mouth percussion classes, Indian mythology/ dance costume and make up workshops.
The final design should communicate a feeling and impression of the vibrance and energy of Indian dance.
Updates
Hi Everyone,
Project Deadline Extended
Reason: I would like to refine a few changes to the details of this lovely design and we have run out of time!
Project Deadline Extended
Reason: Still waiting to hear back form designer re two possible changes to the card design. Tomorrow is the deadline and I have sent several messages but with no response. I need to see this through before selecting this lovely design.
Thank you.
Tara
Industry/Entity Type
Preschool
Requirements
Must have
- The front of the business card should have the photo of me (my face and torso), surrounded entirely by a border of bright magenta (to match the magenta of my lipstick - it is the same as the magenta on my skirt in the second photo). Within the top border I want (perhaps yellow-gold) writing to say "Tara Holloway - Artistic Director" and within the bottom border it should read "Saffron Lantern Indian Dance." If you turn the card on its side the left border should have my telephone number: 0417 862 493 and the right-hand border should read: saffronlanternindiandance@quillmail.example
The reverse of the card should be the orange of the dance costume
and I'd like the picture of my feet and legs to be on the right side of the back of the card as a side border. Centre-aligned on the orange background it should read (perhaps in dark magenta):
Indian dance classes + private tuition
School + preschool educational courses and workshops
Dance theatre performances
Community function workshops and performances
Children's Bollywood parties
Wedding + conference performances
Mouth percussion classes
Indian mythology and dance demonstration workshops
Dance costume and make-up workshops
Nice to have
- A lovely artistic but easy-to-read font would be nice.

```html
<!DOCTYPE html>
<html lang="en">
<head>
<meta charset="utf-8">
<title>Saffron Lantern Indian Dance – Business Card</title>
<link rel="stylesheet" href="https://fonts.googleapis.com/css2?family=Kurale&display=swap">
<style>
  :root {
    --saffron: #e07a2c;
    --saffron-deep: #d96f22;
    --magenta: #d92b91;
    --magenta-text: #c43a8e;
    --silk-plum: #8c1f5a;
    --gold: #e8a23a;
    --white: #ffffff;
    --paper: #ffffff;
  }
  * { margin: 0; padding: 0; box-sizing: border-box; }
  html, body {
    width: 1200px; height: 900px; overflow: hidden;
    background: var(--paper);
    font-family: "Kurale", Georgia, serif;
  }
  .canvas { position: relative; width: 1200px; height: 900px; }

  .card { position: absolute; top: 95px; width: 413px; height: 680px; overflow: hidden; }

  /* Front */
  .card--front { left: 173px; background: var(--saffron); }
  .front-photo {
    position: absolute; left: 110px; top: 0; width: 303px; height: 607px;
    background: linear-gradient(180deg, rgba(140,31,90,0.85) 0%, rgba(200,40,140,0.75) 35%, rgba(232,162,58,0.7) 65%, rgba(200,60,130,0.75) 100%);
    -webkit-mask-image: linear-gradient(90deg, transparent 0%, #000 35%);
            mask-image: linear-gradient(90deg, transparent 0%, #000 35%);
  }
  .front-title {
    position: absolute; left: 0; width: 245px; top: 443px;
    text-align: center; color: var(--magenta-text);
    font-size: 25px; line-height: 32px;
  }
  .front-name {
    position: absolute; left: 0; width: 250px; top: 527px;
    text-align: center; color: var(--magenta-text); font-size: 18px;
  }
  .front-phone-band {
    position: absolute; left: 0; bottom: 0; width: 100%; height: 73px;
    background: var(--magenta);
    display: flex; align-items: center; justify-content: center;
  }
  .front-phone { color: var(--gold); font-size: 46px; letter-spacing: 1px; }

  /* Back */
  .card--back { left: 645px; background: var(--magenta); }
  .back-email-band {
    position: absolute; top: 0; left: 0; width: 100%; height: 77px;
    background: var(--saffron);
    display: flex; align-items: center; justify-content: center;
  }
  .back-email { color: var(--magenta-text); font-size: 15.5px; }
  .services {
    position: absolute; top: 96px; left: 0; width: 100%;
    list-style: none; text-align: center; color: var(--white);
    font-size: 14.5px; line-height: 16px;
  }
  .services li { margin-bottom: 16px; }
  .back-photo {
    position: absolute; left: 42px; top: 445px; width: 355px; height: 235px;
    background: radial-gradient(ellipse at 55% 60%, rgba(232,162,58,0.9) 0%, rgba(224,122,44,0.6) 40%, rgba(217,43,145,0) 72%);
  }
</style>
</head>
<body>
<main class="canvas">
  <section class="card card--front" aria-label="Card front">
    <div class="front-photo" role="img" aria-label="Photograph of a dancer's leg and hennaed foot in a magenta and gold silk costume with ankle bells"></div>
    <h1 class="front-title">Saffron Lantern<br>Indian Dance</h1>
    <p class="front-name">Tara Holloway</p>
    <div class="front-phone-band"><span class="front-phone">0417 862 493</span></div>
  </section>

  <section class="card card--back" aria-label="Card back">
    <div class="back-email-band"><span class="back-email">saffronlanternindiandance@quillmail.example</span></div>
    <ul class="services">
      <li>Indian dance classes + private tuition</li>
      <li>School + preschool educational courses<br>and workshops</li>
      <li>Dance theatre performances</li>
      <li>Community function workshops<br>and performances</li>
      <li>Children's Bollywood parties</li>
      <li>Wedding + conference performances</li>
      <li>Mouth percussion classes</li>
      <li>Indian mythology and dance demonstration<br>workshop</li>
      <li>Dance costume and make-up workshops</li>
    </ul>
    <div class="back-photo" role="img" aria-label="Photograph of the dancer in a gold costume and jewellery, hands raised in a classical pose"></div>
  </section>
</main>
</body>
</html>
```